Stayvora.com banner design

Stayvora.com is looking for a designer to work with ongoing to create a variety of banners.

For this competition we are looking for entrants to create two flash banners with dimensions 300x250 and a static banner/jpg. Each flash banner has two separate concepts one with more copy and more required 'slides' and one with less. The copy for each banner is as follows:

Concept 1: - 4 slide flash banner/animated gif
Save up to 75% on 150,000 Hotels Worldwide.
10% of profits go to local charities.
Do something good when you travel.
End screen call to action - Book now @ stayvora.com (click here)

Concept 1a: 3 slide flash banner/animated gif

Concept 2: 4 slide flash banner/animated gif
$0 Booking fees. Best price guarantee.

Concept 2a: 3 slide flash banner/animated gif

Concept 3 – Static Banner
Book now @ stayvora.com (click here)

Concept 3a

We expect two different designs, one for Concept 1 and 1a and a different design for concept 2 and 2a. Concept 3 (the static banners) can adopt the design used for the flash banners.

We also expect a gif version of the flash banners to be delivered.

The winning entry will then be hired to create each banner in a variety of banner sizes.

Reason: We are not satisfied with the number of entries so are extending this competition. We are looking for a long term relationship with a quality designer to produce a whole range of banners and other designs for stayvora.com.

Industry/Entity Type

Accommodation

Requirements
Must have
• The stayvora.com logo must always be visible on all banners.

Maximum flash file size is 50k
Max Frame Rate 24fps

```html
<!DOCTYPE html>
<html lang="en">
<head>
<meta charset="utf-8">
<title>Stayvora.com banner set</title>
<link rel="stylesheet" href="https://fonts.googleapis.com/css2?family=Arimo:wght@400;700&display=swap">
<style>
  :root {
    --frame-blue: #0a6fc2;
    --sky-blue: #1a78c8;
    --deep-blue: #0b4f9a;
    --pale-blue: #a9d4f2;
    --band-blue: #cfe8f8;
    --text-blue: #0d4f99;
    --orange: #f28c12;
    --orange-light: #ffc255;
    --orange-dark: #c95e00;
    --cta-text: #7a2d00;
    --white: #ffffff;
    --ink: #111111;
    --border: #9a9a9a;
    --pool-dark: #3a2a14;
    --pool-mid: #b08a4a;
    --pool-light: #e7cf8e;
  }
  * { box-sizing: border-box; margin: 0; padding: 0; }
  html, body { width: 1200px; height: 1200px; overflow: hidden; background: var(--white); }
  body { position: relative; font-family: "Arimo", Arial, sans-serif; }

  .gif-set {
    position: absolute; left: 177px; top: 15px; width: 855px; height: 792px;
    border: 8px solid var(--frame-blue);
  }
  .gif-set-title {
    position: absolute; left: 0; right: 0; top: 740px; text-align: center;
    color: var(--orange); font-size: 19px; line-height: 24px;
  }

  .slot { position: absolute; width: 360px; }
  .slot-label { text-align: center; font-size: 19px; color: var(--ink); margin-top: 12px; }

  .banner {
    position: relative; width: 360px; height: 297px; overflow: hidden;
    border: 1px solid var(--border); background: var(--sky-blue);
  }
  .banner--blue {
    background: radial-gradient(ellipse at 30% 20%, #3b9be0 0%, var(--sky-blue) 45%, var(--deep-blue) 100%);
  }

  .top-band {
    position: absolute; left: 0; top: 0; width: 100%; height: 74px;
    background: linear-gradient(to bottom, var(--band-blue), var(--pale-blue));
    display: flex; align-items: center; justify-content: center; gap: 8px;
  }
  .big-figure {
    font-weight: 700; color: var(--orange); font-size: 54px; letter-spacing: -2px; line-height: 1;
    text-shadow: 1px 1px 0 var(--orange-dark);
  }
  .band-copy { color: var(--text-blue); font-weight: 700; font-size: 20px; line-height: 1.1; }

  .headline {
    position: absolute; left: 56px; top: 10px; color: var(--white); font-weight: 700;
    text-shadow: 1px 1px 2px rgba(0,0,0,.6);
  }
  .headline .line-1, .headline .line-2 { font-size: 23px; line-height: 1.05; }
  .headline .line-3 { font-size: 15px; line-height: 1.2; }
  .headline .pct {
    position: absolute; left: 146px; top: -4px; font-size: 58px; color: var(--orange);
    letter-spacing: -2px; text-shadow: 1px 1px 0 var(--orange-dark);
  }

  .photo-stack { position: absolute; left: 0; width: 100%; height: 130px; }
  .photo {
    position: absolute; width: 104px; height: 112px; border: 5px solid var(--white);
    box-shadow: 2px 3px 6px rgba(0,0,0,.45);
  }
  .photo--dome { left: 22px; top: 8px; transform: rotate(-6deg);
    background: linear-gradient(to bottom, #8ec7ea, #d8e6ee 55%, #3d8fc4); }
  .photo--resort { left: 128px; top: 0; transform: rotate(2deg);
    background: linear-gradient(to bottom, #b9d9ee, #e4e1d4 45%, #5f9a4e 70%, #2e9bd0); }
  .photo--tower { left: 232px; top: 6px; transform: rotate(7deg);
    background: linear-gradient(to bottom, #c7dff0, #eef0f2 40%, #7fa5b8 75%, #7a5a3a); }

  .pool-scene {
    position: absolute; left: 0; width: 100%;
    background: linear-gradient(to bottom, var(--pool-dark) 0%, #7b5a2c 25%, var(--pool-light) 45%, var(--pool-mid) 65%, var(--pool-dark) 100%);
  }

  .book-line {
    position: absolute; left: 0; right: 0; text-align: center; color: var(--white);
    font-weight: 700; font-size: 17px; text-shadow: 1px 1px 2px rgba(0,0,0,.7);
  }

  .swoosh { position: absolute; left: 0; bottom: 0; width: 360px; height: 90px; }

  .cta {
    position: absolute; left: 84px; top: 205px; width: 186px; height: 44px; border-radius: 7px;
    background: linear-gradient(to bottom, var(--orange-light), var(--orange) 55%, #e27400);
    box-shadow: 0 2px 4px rgba(0,0,0,.4);
    display: flex; align-items: center; justify-content: center; gap: 10px;
    color: var(--cta-text); font-weight: 700; font-size: 20px;
  }
  .cta-arrow {
    width: 26px; height: 26px; border-radius: 4px; background: var(--cta-text);
    display: flex; align-items: center; justify-content: center;
  }

  .brand {
    position: absolute; left: 0; bottom: 0; width: 100%; height: 34px;
    display: flex; align-items: center; justify-content: center; gap: 7px;
  }
  .brand-dot { width: 16px; height: 16px; border-radius: 50%; background: var(--orange); }
  .brand-name { font-size: 19px; font-weight: 700; color: var(--deep-blue); }
</style>
</head>
<body>

<svg width="0" height="0" style="position:absolute">
  <defs>
    <symbol id="swoosh" viewBox="0 0 360 90" preserveAspectRatio="none">
      <path d="M0 22 Q180 72 360 22 L360 90 L0 90 Z" fill="#f28c12"/>
      <path d="M0 34 Q180 82 360 34 L360 90 L0 90 Z" fill="#ffffff"/>
    </symbol>
    <symbol id="play" viewBox="0 0 10 10"><path d="M3 2 L8 5 L3 8 Z" fill="#ffffff"/></symbol>
  </defs>
</svg>

<section class="gif-set">
  <p class="gif-set-title">Animated Gif Version</p>
</section>

<!-- Banner 1 -->
<div class="slot" style="left:243px; top:36px;">
  <div class="banner banner--blue">
    <div class="headline">
      <div class="line-1">SAVE UP TO</div>
      <div class="line-2">ON 150,000</div>
      <div class="line-3">HOTELS WORLDWIDE</div>
      <div class="pct">75%</div>
    </div>
    <div class="photo-stack" style="top:88px;">
      <div class="photo photo--dome" role="img" aria-label="Hotel with glass dome"></div>
      <div class="photo photo--resort" role="img" aria-label="Resort with pool and palms"></div>
      <div class="photo photo--tower" role="img" aria-label="Hotel tower with balconies"></div>
    </div>
    <svg class="swoosh"><use href="#swoosh"/></svg>
    <div class="cta">CLICK HERE <span class="cta-arrow"><svg width="16" height="16"><use href="#play"/></svg></span></div>
    <div class="brand"><span class="brand-dot"></span><span class="brand-name">Stayvora.com</span></div>
  </div>
  <p class="slot-label">300X250 banner 1</p>
</div>

<!-- Banner 1a -->
<div class="slot" style="left:618px; top:36px;">
  <div class="banner banner--blue">
    <div class="top-band"><span class="big-figure">10%</span><span class="band-copy">of Profits Go to<br>Local Charities</span></div>
    <div class="photo-stack" style="top:88px;">
      <div class="photo photo--dome" role="img" aria-label="Hotel with glass dome"></div>
      <div class="photo photo--resort" role="img" aria-label="Resort with pool and palms"></div>
      <div class="photo photo--tower" role="img" aria-label="Hotel tower with balconies"></div>
    </div>
    <svg class="swoosh"><use href="#swoosh"/></svg>
    <div class="cta" style="top:215px;">CLICK HERE <span class="cta-arrow"><svg width="16" height="16"><use href="#play"/></svg></span></div>
    <div class="brand"><span class="brand-dot"></span><span class="brand-name">Stayvora.com</span></div>
  </div>
  <p class="slot-label">300X250 banner 1a</p>
</div>

<!-- Banner 2 -->
<div class="slot" style="left:243px; top:399px;">
  <div class="banner">
    <div class="pool-scene" style="top:74px; height:223px;" role="img" aria-label="Indoor hotel pool hall with columns"></div>
    <div class="top-band"><span class="big-figure">$0</span><span class="band-copy">booking fees.<br>best price guarantee.</span></div>
    <svg class="swoosh"><use href="#swoosh"/></svg>
    <div class="cta">CLICK HERE <span class="cta-arrow"><svg width="16" height="16"><use href="#play"/></svg></span></div>
    <div class="brand"><span class="brand-dot"></span><span class="brand-name">Stayvora.com</span></div>
  </div>
  <p class="slot-label">300X250 banner 2</p>
</div>

<!-- Banner 2a -->
<div class="slot" style="left:618px; top:399px;">
  <div class="banner">
    <div class="pool-scene" style="top:0; height:297px;" role="img" aria-label="Indoor hotel pool hall with columns"></div>
    <div class="headline" style="top:24px; left:16px;">
      <div class="line-1">SAVE UP TO</div>
      <div class="line-2">ON 150,000</div>
      <div class="line-3">HOTELS WORLDWIDE</div>
      <div class="pct">75%</div>
    </div>
    <svg class="swoosh"><use href="#swoosh"/></svg>
    <div class="cta">CLICK HERE <span class="cta-arrow"><svg width="16" height="16"><use href="#play"/></svg></span></div>
    <div class="brand"><span class="brand-dot"></span><span class="brand-name">Stayvora.com</span></div>
  </div>
  <p class="slot-label">300X250 banner 2a</p>
</div>

<!-- Banner 3 -->
<div class="slot" style="left:243px; top:861px;">
  <div class="banner">
    <div class="pool-scene" style="top:0; height:297px;" role="img" aria-label="Indoor hotel pool hall with columns"></div>
    <div class="headline" style="top:24px; left:52px;">
      <div class="line-1">SAVE UP TO</div>
      <div class="line-2">ON 150,000</div>
      <div class="line-3">HOTELS WORLDWIDE</div>
      <div class="pct">75%</div>
    </div>
    <p class="book-line" style="top:174px;">Book Now@stayvora.com</p>
    <svg class="swoosh"><use href="#swoosh"/></svg>
    <div class="cta">CLICK HERE <span class="cta-arrow"><svg width="16" height="16"><use href="#play"/></svg></span></div>
    <div class="brand"><span class="brand-dot"></span><span class="brand-name">Stayvora.com</span></div>
  </div>
  <p class="slot-label">300X250 banner 3</p>
</div>

<!-- Banner 3a -->
<div class="slot" style="left:618px; top:861px;">
  <div class="banner banner--blue">
    <div class="top-band"><span class="big-figure">10%</span><span class="band-copy">of Profits Go to<br>Local Charities</span></div>
    <p class="book-line" style="top:86px;">Book Now@stayvora.com</p>
    <div class="photo-stack" style="top:118px; transform:scale(.82); transform-origin:50% 0;">
      <div class="photo photo--dome" role="img" aria-label="Hotel with glass dome"></div>
      <div class="photo photo--resort" role="img" aria-label="Resort with pool and palms"></div>
      <div class="photo photo--tower" role="img" aria-label="Hotel tower with balconies"></div>
    </div>
    <svg class="swoosh"><use href="#swoosh"/></svg>
    <div class="cta" style="top:215px;">CLICK HERE <span class="cta-arrow"><svg width="16" height="16"><use href="#play"/></svg></span></div>
    <div class="brand"><span class="brand-dot"></span><span class="brand-name">Stayvora.com</span></div>
  </div>
  <p class="slot-label">300X250 banner 3a</p>
</div>

</body>
</html>
```